Brimlow Plumbing Solutions

This is for my new plumbing company, I have attached an example of what I’m going for but want it to look better.

Target Market(s)

Home owners, real estate, etc.

Industry/Entity Type

Plumbing

Font styles to use
Other font styles liked:
• As per my logo and other examples uploaded

Colors

Designer to choose colors to be used in the design.

Requirements
Must have
• Must include my logo provided and similar to my flyer I have attached but better

```html
<!DOCTYPE html>
<html lang="en">
<head>
<meta charset="utf-8">
<title>Brimlow Plumbing Solutions – Flyer</title>
<link rel="stylesheet" href="https://fonts.googleapis.com/css2?family=Montserrat:wght@500;600;700;800&family=Arimo:wght@400;700&display=swap">
<style>
  :root {
    --stage: #d8d8da;
    --ink: #1d1d1f;
    --blue: #1f57c2;
    --blue-bright: #3d86e0;
    --tile: #eeecf5;
    --white: #ffffff;
    --rule: #4a4a4e;
  }
  * { box-sizing: border-box; margin: 0; padding: 0; }
  html, body {
    width: 1200px; height: 800px; overflow: hidden;
    background: var(--stage);
  }
  .flyer {
    position: absolute; left: 330px; top: 18px;
    width: 540px; height: 764px;
    background: var(--ink);
    font-family: "Montserrat", sans-serif;
    display: flex; flex-direction: column;
    overflow: hidden;
  }
  .masthead {
    height: 120px; position: relative;
    display: flex; align-items: center; padding-left: 28px;
  }
  .brand { display: flex; align-items: center; gap: 12px; }
  .brand-dot {
    width: 44px; height: 44px; border-radius: 50%;
    background: var(--blue-bright);
  }
  .brand-name {
    color: var(--white); font-weight: 800;
    font-size: 19px; line-height: 1.1; letter-spacing: .5px;
    text-transform: uppercase;
  }
  .offer-badge {
    position: absolute; right: 26px; top: 8px;
    width: 150px; height: 150px; z-index: 2;
  }
  .offer-badge svg { position: absolute; inset: 0; }
  .offer-text {
    position: absolute; inset: 0;
    display: flex; flex-direction: column; align-items: center; justify-content: center;
    color: var(--white); text-align: center; transform: rotate(-12deg);
  }
  .offer-lead { font-size: 9px; font-weight: 800; line-height: 1.2; text-transform: uppercase; }
  .offer-value { font-size: 34px; font-weight: 800; line-height: 1; margin: 2px 0; }
  .offer-label { font-size: 10px; font-weight: 600; letter-spacing: 4px; text-transform: uppercase; }
  .tagline-band {
    height: 70px; background: var(--blue);
    display: flex; align-items: center; padding: 0 28px;
    color: var(--white); font-family: "Arimo", sans-serif;
    font-size: 17px; line-height: 1.3;
  }
  .tagline-band strong { font-weight: 700; }
  .services-heading {
    height: 44px; display: flex; align-items: center; gap: 14px;
    padding: 0 29px;
  }
  .services-heading .rule { flex: 1; height: 2px; background: var(--rule); }
  .services-heading h2 {
    color: var(--blue-bright); font-size: 20px; font-weight: 800;
    letter-spacing: 1px; text-transform: uppercase;
  }
  .service-grid {
    display: grid; grid-template-columns: repeat(3, 150px);
    grid-auto-rows: 146px; gap: 14px 16px;
    padding: 4px 29px 0; flex: 1;
  }
  .service-tile {
    background: var(--tile); border-radius: 10px;
    display: flex; flex-direction: column; align-items: center; justify-content: center;
    gap: 12px; text-align: center;
  }
  .service-icon {
    width: 62px; height: 56px; border-radius: 8px;
    background: linear-gradient(160deg, var(--blue-bright), var(--blue));
  }
  .service-name {
    color: var(--ink); font-size: 13px; font-weight: 500; line-height: 1.2;
  }
  .contact-band {
    height: 50px; background: var(--blue);
    display: flex; align-items: center; gap: 22px; padding: 0 24px;
    color: var(--white); font-size: 13px; font-weight: 600;
  }
  .contact-item { display: flex; align-items: center; gap: 7px; }
  .contact-item svg { width: 18px; height: 18px; }
  .social { margin-left: auto; display: flex; gap: 8px; }
  .social-square { width: 20px; height: 20px; border-radius: 4px; background: var(--white); opacity: .9; }
</style>
</head>
<body>
  <main class="flyer">
    <header class="masthead">
      <div class="brand">
        <span class="brand-dot"></span>
        <div class="brand-name">Brimlow<br>Plumbing Solutions</div>
      </div>
      <div class="offer-badge">
        <svg viewBox="0 0 150 150" aria-hidden="true">
          <g fill="#3d86e0">
            <rect x="30" y="30" width="90" height="90" transform="rotate(0 75 75)"/>
            <rect x="30" y="30" width="90" height="90" transform="rotate(22.5 75 75)"/>
            <rect x="30" y="30" width="90" height="90" transform="rotate(45 75 75)"/>
            <rect x="30" y="30" width="90" height="90" transform="rotate(67.5 75 75)"/>
          </g>
        </svg>
        <div class="offer-text">
          <span class="offer-lead">Mention this<br>flyer to receive</span>
          <span class="offer-value">15%</span>
          <span class="offer-label">Discount</span>
        </div>
      </div>
    </header>

    <section class="tagline-band">
      <p>Your local reliable Sydney plumber - Specialising in all aspects of <strong>Plumbing, Drainage &amp; Gas Maintenance.</strong></p>
    </section>

    <div class="services-heading">
      <span class="rule"></span>
      <h2>Our Services:</h2>
      <span class="rule"></span>
    </div>

    <section class="service-grid">
      <div class="service-tile"><div class="service-icon" role="img" aria-label="Emergency plumbing icon"></div><p class="service-name">Emergency<br>plumbing</p></div>
      <div class="service-tile"><div class="service-icon" role="img" aria-label="Plumbing maintenance icon"></div><p class="service-name">Plumbing<br>Maintenance</p></div>
      <div class="service-tile"><div class="service-icon" role="img" aria-label="Drainage maintenance icon"></div><p class="service-name">Drainage<br>Maintenance</p></div>
      <div class="service-tile"><div class="service-icon" role="img" aria-label="Gas maintenance icon"></div><p class="service-name">Gas<br>Maintenance</p></div>
      <div class="service-tile"><div class="service-icon" role="img" aria-label="Hot water system icon"></div><p class="service-name">Hot water<br>Systems</p></div>
      <div class="service-tile"><div class="service-icon" role="img" aria-label="Leaking fixtures icon"></div><p class="service-name">Leaking<br>Fixtures</p></div>
      <div class="service-tile"><div class="service-icon" role="img" aria-label="Blocked sewer and stormwater icon"></div><p class="service-name">Blocked sewer<br>&amp; stormwater</p></div>
      <div class="service-tile"><div class="service-icon" role="img" aria-label="Camera and locating icon"></div><p class="service-name">Camera<br>&amp; Locating</p></div>
      <div class="service-tile"><div class="service-icon" role="img" aria-label="TMV maintenance icon"></div><p class="service-name">TMV<br>Maintenance</p></div>
    </section>

    <footer class="contact-band">
      <span class="contact-item">
        <svg viewBox="0 0 24 24" aria-hidden="true"><circle cx="12" cy="12" r="12" fill="#3d86e0"/><path d="M8.5 6.5l2 2.2-1.2 1.5c.8 1.7 2 2.9 3.6 3.7l1.5-1.2 2.2 2-1.2 2c-4.2-.3-8.1-4.2-8.4-8.4z" fill="#fff"/></svg>
        0400 555 019
      </span>
      <span class="contact-item">
        <svg viewBox="0 0 24 24" aria-hidden="true"><circle cx="12" cy="12" r="12" fill="#3d86e0"/><rect x="6" y="8" width="12" height="8" fill="none" stroke="#fff" stroke-width="1.4"/><path d="M6 8l6 4.5L18 8" fill="none" stroke="#fff" stroke-width="1.4"/></svg>
        hello@brimlowplumbing.com.au
      </span>
      <span class="social">
        <span class="social-square"></span>
        <span class="social-square"></span>
      </span>
    </footer>
  </main>
</body>
</html>
```